Realtor branding business card

modern, simple and self branding. Broker office logo needs to be used but not emphasized. Looking to brand myself

Target Market(s)

buyers, sellers and investors

Industry/Entity Type

Realtor

Contact Information for Business Card

Sample of my current business card on file

Requirements
Must have
• my website - tobiasmerrowkl.com
• Realtor logo
• Fair housing logo
Nice to have
• Colors from office logo but not a must
Should not have
• Do not want headshot

```html
<!DOCTYPE html>
<html lang="en">
<head>
<meta charset="utf-8">
<title>Tobias Merrow – Business Card</title>
<link href="https://fonts.googleapis.com/css2?family=Montserrat:wght@400;600;800&display=swap" rel="stylesheet">
<style>
  :root {
    --navy: #2e2a72;
    --navy-light: #3d3a86;
    --red: #d9292b;
    --white: #ffffff;
    --grey-text: #6b6b78;
    --backdrop: #d4d4d4;
    --badge: rgba(255,255,255,0.88);
  }
  * { box-sizing: border-box; margin: 0; padding: 0; }
  html, body {
    width: 1200px; height: 930px; overflow: hidden;
    background: var(--backdrop);
    font-family: "Montserrat", sans-serif;
  }
  .stage {
    position: relative; width: 1200px; height: 930px;
    display: flex; align-items: center; justify-content: center; gap: 40px;
  }
  .card {
    position: relative; width: 540px; height: 309px; overflow: hidden;
    box-shadow: 0 6px 18px rgba(0,0,0,0.18);
  }

  /* Back side */
  .card--back {
    background: linear-gradient(100deg, var(--navy) 0%, var(--navy-light) 45%, var(--navy) 100%);
    color: var(--white);
  }
  .card--back .brand {
    position: absolute; left: 0; right: 0; top: 118px;
    text-align: center; font-weight: 600; font-size: 26px; line-height: 1.1;
    color: var(--white); letter-spacing: 0.5px;
  }
  .card--back .brand small { display: block; font-size: 15px; font-weight: 600; }
  .card--back .website {
    position: absolute; left: 0; right: 0; bottom: 34px;
    text-align: center; font-size: 13px; letter-spacing: 0.5px;
  }

  /* Front side */
  .card--front { background: var(--white); }
  .card--front .band { position: absolute; inset: 0; }
  .card--front .brand {
    position: absolute; right: 30px; top: 30px; text-align: right;
    font-weight: 600; font-size: 15px; line-height: 1.15; color: var(--navy);
  }
  .card--front .brand small { display: block; font-size: 11px; font-weight: 600; }
  .agent { position: absolute; left: 36px; top: 92px; }
  .agent-name { font-weight: 800; font-size: 22px; color: var(--navy); letter-spacing: 0.6px; }
  .agent-title { font-size: 13px; color: var(--grey-text); margin-top: 4px; }
  .address {
    position: absolute; left: 36px; top: 150px;
    font-size: 12px; line-height: 1.45; color: var(--grey-text);
  }
  .contacts {
    position: absolute; left: 36px; top: 218px; list-style: none;
    color: var(--white); font-size: 12.5px; line-height: 1;
  }
  .contacts li { display: flex; align-items: center; gap: 10px; margin-bottom: 7px; }
  .contacts svg { width: 12px; height: 12px; flex: none; }
  .badges {
    position: absolute; right: 30px; bottom: 24px;
    display: flex; gap: 12px;
  }
  .badge { width: 38px; height: 38px; background: var(--badge); border-radius: 4px; }
</style>
</head>
<body>
<main class="stage">
  <section class="card card--back" aria-label="Card back">
    <div class="brand">Northgate<small>Realty Group</small></div>
    <div class="website">www.tobiasmerrowkl.com</div>
  </section>

  <section class="card card--front" aria-label="Card front">
    <svg class="band" viewBox="0 0 540 309" preserveAspectRatio="none" aria-hidden="true">
      <defs>
        <linearGradient id="bandFill" x1="0" x2="1" y1="0" y2="0">
          <stop offset="0" stop-color="#2e2a72"/>
          <stop offset="0.5" stop-color="#3d3a86"/>
          <stop offset="1" stop-color="#2e2a72"/>
        </linearGradient>
      </defs>
      <polygon points="0,205 540,150 540,309 0,309" fill="url(#bandFill)"/>
    </svg>
    <div class="brand">Northgate<small>Realty Group</small></div>
    <div class="agent">
      <div class="agent-name">TOBIAS MERROW</div>
      <div class="agent-title">Realtor</div>
    </div>
    <div class="address">480 Cedarbrook Lane<br>Lake Harmon, FL 32790</div>
    <ul class="contacts">
      <li><svg viewBox="0 0 12 12"><rect x="3" y="0.5" width="6" height="11" rx="1" fill="none" stroke="#fff"/><circle cx="6" cy="9.5" r="0.7" fill="#fff"/></svg>555.218.4406</li>
      <li><svg viewBox="0 0 12 12"><path d="M2 1l2.5 0 1 3-1.5 1a7 7 0 0 0 3 3l1-1.5 3 1V10a1.5 1.5 0 0 1-1.5 1.5A9 9 0 0 1 .5 2.5 1.5 1.5 0 0 1 2 1z" fill="#fff"/></svg>555.630.1200</li>
      <li><svg viewBox="0 0 12 12"><rect x="0.5" y="2.5" width="11" height="7" fill="none" stroke="#fff"/><path d="M0.5 2.5L6 7l5.5-4.5" fill="none" stroke="#fff"/></svg>info@tobiasmerrowkl.com</li>
      <li><svg viewBox="0 0 12 12"><circle cx="6" cy="6" r="5.3" fill="none" stroke="#fff"/><ellipse cx="6" cy="6" rx="2.3" ry="5.3" fill="none" stroke="#fff"/><path d="M0.7 6h10.6" stroke="#fff"/></svg>www.tobiasmerrowkl.com</li>
    </ul>
    <div class="badges">
      <div class="badge" role="img" aria-label="Realtor membership badge"></div>
      <div class="badge" role="img" aria-label="Fair housing badge"></div>
    </div>
  </section>
</main>
</body>
</html>
```